Window Treatment business needs website redesigned.

We need a revamp and refresh of our current site www.velmarix.ca
Looking to attract very high end customer. It should be a very simple design with very little text. This site will be visited by prospective homeowners, designers, builders and architects. They should feel that they are dealing with a high-end product selection, where experience, customer service and unique product offering is the focus. The content will be to highlight our services and highlight the manufacturers we sell, using a few rich photos to highlight the products. We should NOT look like we are a very large company. It should NOT have discounts/savings buttons and many menus to choose from. We offer over 15 years experience to narrow the many market options, to provide the right technical solution.
We specialize in products that are not readily available on the market and specifically motorized systems for indoors and outdoors.
Our main suppliers are Kravenholt.com, Dimbrell.com
We carry our own locally manufactured product line of roller shades.
Main product pictures should be of roller shades, outdoor bug screens, awnings and outdoor pergolas.

Reason: I understand that Christmas is coming up real short and many people are extremely busy. If you have a CREATIVE gifting you still want to submit, I look forward to your idea!

Reason: Due to holiday season, we have not had sufficient time to review to make a final decision. Thank you for your patience!

Target Market(s)

High end home owners, designers, builders, architects

Industry/Entity Type

Contractor

Coding

Coded - Design and coding required

Number of Pages Required

3 page

Font styles to use
Sans Serif

Requirements
Must have
• Landing page with full size image like homepage of zolvane.it
• Products page that highlights products with simple product shot image, description and link to manufacturer.
• On main page a scrolling of customer reviews.
• I want a very simple, eye-catching, emotional image for homepage. It does not need to include any product image.
• An image that shows technology combining/meshing with hand craftsmanship.
• Focus is on design.
• http://www.zolvane.it/en/gallery is a great layout and design.
Nice to have
• Logo shape for icons and watermark should be used.
• Look like and have simple motion effects like quorix.com or telvarin.com
Should not have
• Generic/standard looking feel like bluppet.com or mecklorwindow.ca
• No use of green as background only subtle text.
• Lots of text and pages.

```html
<!DOCTYPE html>
<html lang="en">
<head>
<meta charset="utf-8">
<title>Velmarix — Window Treatment Solutions</title>
<link href="https://fonts.googleapis.com/css2?family=Roboto:ital,wght@0,400;0,500;0,700;1,400&family=Caveat:wght@400&display=swap" rel="stylesheet">
<style>
:root{
  --green:#5cb54a;
  --green-dot:#9fcf7a;
  --ink:#2f3236;
  --band-dark:#4a4b4d;
  --mail-bg:#37424a;
  --light:#f3f4f6;
  --footer-top:#3a3b3d;
  --footer-bottom:#4e5052;
  --label-bg:rgba(255,255,255,.86);
  --muted:#6d6f72;
}
*{box-sizing:border-box;margin:0;padding:0}
html,body{width:1200px;height:2296px;overflow:hidden}
body{position:relative;font-family:'Roboto',Arial,sans-serif;color:var(--ink);background:#fff}
.abs{position:absolute}

/* hero */
.hero{left:0;top:0;width:1200px;height:544px;
  background:
    radial-gradient(ellipse 260px 120px at 470px 380px,rgba(236,196,140,.75),rgba(236,196,140,0) 70%),
    radial-gradient(ellipse 300px 90px at 900px 300px,rgba(255,214,150,.35),rgba(255,214,150,0) 70%),
    radial-gradient(ellipse 420px 200px at 470px 250px,rgba(235,238,242,.55),rgba(235,238,242,0) 70%),
    linear-gradient(180deg,#3f5270 0%,#6d8099 25%,#8d9db1 42%,#5b6579 55%,#4c4a4c 70%,#6a5849 85%,#3b322b 100%)}
.hero-device{left:0;top:207px;width:207px;height:295px;border-radius:0 14px 14px 0;
  background:linear-gradient(160deg,#1f2123 0%,#2c2f32 8%,#d9dde2 9%,#eef1f4 40%,#c9d3dc 90%,#1f2123 91%)}
.site-header{left:0;top:0;width:1200px;height:67px;background:rgba(255,255,255,.1);border-bottom:1px solid rgba(255,255,255,.3)}
.brand{left:43px;top:13px;display:flex;align-items:center;gap:10px}
.brand-dot{width:40px;height:40px;border-radius:50%;border:3px solid #fff}
.brand-name{font-size:28px;font-weight:500;color:#fff}
.nav{top:24px;font-size:16px;font-weight:500;color:#fff}
.btn-pill{top:16px;height:33px;border-radius:17px;font-size:13px;display:flex;align-items:center;justify-content:center}
.btn-login{left:963px;width:61px;border:1.5px solid #fff;color:#fff}
.btn-quote{left:1033px;width:120px;background:#fff;color:#222}
.hero-title{right:52px;top:214px;font-family:'Caveat',cursive;font-size:100px;color:#fff;line-height:1}
.hero-sub{right:63px;top:330px;text-align:right;font-size:21px;font-weight:700;color:#fff;line-height:27px;text-shadow:0 1px 3px rgba(0,0,0,.4)}

/* intro band */
.intro{left:0;top:544px;width:1200px;height:110px;background:var(--band-dark);color:#fff;text-align:center}
.intro h1{position:absolute;left:0;width:1200px;top:4px;font-size:23px;font-weight:700}
.intro .rule{position:absolute;left:52px;width:1096px;top:42px;border-top:1.5px dotted #ddd}
.intro p{position:absolute;left:70px;width:1060px;top:59px;font-size:13px;line-height:20px}

/* products */
.products{left:0;top:654px;width:1200px;height:308px;background:var(--light)}
.tab{font-size:19px;font-weight:500}
.tab-indoor{left:509px;top:20px}
.tab-outdoor{left:599px;top:9px;width:105px;height:44px;border:1.5px solid var(--green);border-radius:3px;color:var(--green);display:flex;align-items:center;justify-content:center;background:#fff}
.green-rule{left:52px;width:1096px;border-top:2px dotted var(--green-dot)}
.card{top:113px;width:253px;height:147px}
.card-photo{position:absolute;left:0;top:0;width:253px;height:126px;border-radius:3px}
.card-label{position:absolute;left:10px;top:106px;width:233px;height:41px;background:linear-gradient(#5a5b5d,#3f4042);border-radius:3px;color:#fff;font-size:17px;font-weight:500;display:flex;align-items:center;justify-content:center;box-shadow:0 2px 4px rgba(0,0,0,.3)}
.card-icon{position:absolute;left:100px;top:-20px;width:52px;height:52px;border-radius:50%;background:#fff;border:3px solid #222}

/* mail */
.mail{left:0;top:962px;width:600px;height:358px;background:var(--mail-bg)}
.mail h2{position:absolute;left:0;width:600px;top:22px;text-align:center;color:#fff;font-size:28px;font-weight:500}
.field{background:#fff;border-radius:3px;font-size:13px;color:#9a9a9a;padding:9px 12px}
.btn-send{left:233px;top:295px;width:134px;height:31px;background:var(--green);color:#fff;font-size:13px;font-weight:500;display:flex;align-items:center;justify-content:center;border-radius:2px}
.door{left:600px;top:962px;width:600px;height:358px;
  background:
    radial-gradient(ellipse 180px 200px at 300px 150px,rgba(186,205,160,.8),rgba(186,205,160,0) 75%),
    linear-gradient(90deg,#4a3a28 0%,#6b5638 12%,#2a2d28 20%,#6f8659 35%,#92a676 50%,#6f8659 65%,#2a2d28 80%,#6b5638 90%,#4a3a28 100%)}
.door-floor{left:600px;top:1250px;width:600px;height:70px;background:linear-gradient(180deg,rgba(60,60,58,0),#2b2b29 60%)}
.mail-mark{left:560px;top:1105px;width:80px;height:80px;border-radius:50%;background:#fff;border:5px solid #222}
.hotspot{font-size:13px;color:#222;background:var(--label-bg);padding:3px 7px;line-height:16px}
.plus{width:17px;height:17px}

/* projects */
.section-title{left:0;width:1200px;text-align:center;font-size:23px;font-weight:700;color:var(--ink)}
.section-title span{color:var(--green)}
.project{top:1398px;width:240px;height:188px}

/* testimonials */
.reviews{left:0;top:1616px;width:1200px;height:202px;background:var(--light)}
.quote{font-size:13px;font-style:italic;color:var(--muted);line-height:19px}
.reviewer{font-size:13px;font-weight:500;color:#333}
.avatar{width:76px;height:76px;border-radius:50%;border:3px solid #fff;box-shadow:0 0 0 1px #ccc}

/* like bar */
.like-rule{left:67px;top:1857px;width:1066px;border-top:1px solid #ddd}
.like-pill{left:377px;top:1834px;width:448px;height:46px;background:#fff;border:1px solid #ddd;border-radius:23px}
.like-btn{left:498px;top:1848px;height:20px;padding:0 6px;background:#4267b2;color:#fff;font-size:11px;font-weight:700;border-radius:2px;display:flex;align-items:center;gap:4px}
.like-text{left:550px;top:1851px;font-size:11px;color:#333}

/* footer */
.footer{left:0;top:1894px;width:1200px;height:402px;background:linear-gradient(180deg,var(--footer-top),var(--footer-bottom))}
.footer h3{position:absolute;font-size:18px;font-weight:700;color:#fff}
.footer p,.footer .line{position:absolute;font-size:13px;color:#fff;line-height:19px}
.footer strong{font-weight:700}
.social{width:14px;height:14px;border-radius:50%;background:#fff}
.map{left:334px;top:60px;width:534px;height:227px;background:linear-gradient(135deg,#ebe8e0 0%,#dfe4e6 50%,#e4e8dc 100%)}
.footer-rule{left:52px;top:340px;width:1096px;border-top:1px solid rgba(255,255,255,.4)}
.footer-small{top:375px;font-size:12px;font-weight:700;color:#fff}
</style>
</head>
<body>

<section class="abs hero" role="img" aria-label="Modern white pavilion with lounge furniture on a rooftop terrace overlooking a city skyline at dusk"></section>
<div class="abs hero-device" role="img" aria-label="Tablet showing a shade control app"></div>

<header class="abs site-header">
  <div class="abs brand"><span class="brand-dot"></span><span class="brand-name">Velmarix</span></div>
  <nav>
    <span class="abs nav" style="left:412px">ABOUT</span>
    <span class="abs nav" style="left:502px">SERVICES</span>
    <span class="abs nav" style="left:613px">GALLERY</span>
    <span class="abs nav" style="left:717px">CONTACT</span>
  </nav>
  <span class="abs btn-pill btn-login">Log In</span>
  <span class="abs btn-pill btn-quote">Request a Quote</span>
</header>

<div class="abs hero-title">Pavilion</div>
<div class="abs hero-sub">Modern wind and rain systems<br>with aluminum or fabric roof systems</div>

<section class="abs intro">
  <h1>Velmarix Windows Treatment Solutions</h1>
  <div class="rule"></div>
  <p>At Velmarix we specialize in custom high quality window treatments. Whether it is for a condo, home or entire building, we provide free sampling, free on site consultation and turnkey installation services to Toronto, the entire GTA and northern cottage community.</p>
</section>

<section class="abs products">
  <span class="abs tab tab-indoor">Indoor</span>
  <span class="abs tab tab-outdoor">Outdoor</span>
  <div class="abs green-rule" style="top:62px"></div>

  <div class="abs card" style="left:52px">
    <div class="card-photo" role="img" aria-label="Living room with roller shades on large windows" style="background:radial-gradient(ellipse 50px 40px at 30px 60px,rgba(255,220,150,.8),rgba(255,220,150,0)),linear-gradient(90deg,#6e5a44 0%,#a89276 25%,#d9d3c6 45%,#8fa3b5 60%,#cfc2a8 75%,#8a7458 100%)"></div>
    <div class="card-icon"><svg width="46" height="46" viewBox="0 0 46 46"><rect x="14" y="13" width="18" height="18" fill="none" stroke="#222" stroke-width="2"/><rect x="14" y="13" width="18" height="10" fill="#222"/></svg></div>
    <div class="card-label">Shades</div>
  </div>
  <div class="abs card" style="left:332px">
    <div class="card-photo" role="img" aria-label="Cream drapery panels in a bright room" style="background:linear-gradient(90deg,#7a6446 0%,#e6d3a8 15%,#f5ecd8 30%,#d8c39a 42%,#f3ead6 55%,#d6c095 68%,#f1e6cf 82%,#8a7048 100%)"></div>
    <div class="card-icon"><svg width="46" height="46" viewBox="0 0 46 46"><line x1="12" y1="13" x2="34" y2="13" stroke="#222" stroke-width="2"/><path d="M14 14 L14 32 L20 32 Q17 22 22 14Z M32 14 L32 32 L26 32 Q29 22 24 14Z" fill="#222"/></svg></div>
    <div class="card-label">Drapery</div>
  </div>
  <div class="abs card" style="left:614px">
    <div class="card-photo" role="img" aria-label="Patio with bug screens overlooking a lake and hills" style="background:linear-gradient(180deg,#b9772e 0%,#d99a4a 22%,#a7c0d8 40%,#7f98ad 58%,#6d8a5a 75%,#4b5e3a 100%)"></div>
    <div class="card-icon"><svg width="46" height="46" viewBox="0 0 46 46"><rect x="13" y="13" width="20" height="18" fill="none" stroke="#222" stroke-width="2"/><rect x="13" y="13" width="20" height="6" fill="#222"/></svg></div>
    <div class="card-label">Bug Screens</div>
  </div>
  <div class="abs card" style="left:894px">
    <div class="card-photo" role="img" aria-label="Outdoor awning over a seaside terrace" style="background:linear-gradient(180deg,#6fa2d6 0%,#a9c8e6 30%,#e6edf2 52%,#8cb9cf 66%,#2f86b0 82%,#d8d2c4 100%)"></div>
    <div class="card-icon"><svg width="46" height="46" viewBox="0 0 46 46"><path d="M12 20 L15 13 L31 13 L34 20Z" fill="#222"/><rect x="14" y="20" width="18" height="12" fill="none" stroke="#222" stroke-width="2"/></svg></div>
    <div class="card-label">Awnings</div>
  </div>
</section>

<section class="abs mail">
  <h2>Feel Free to Mail</h2>
  <div class="abs field" style="left:50px;top:79px;width:240px;height:31px">Name *</div>
  <div class="abs field" style="left:311px;top:79px;width:240px;height:31px">Email *</div>
  <div class="abs field" style="left:50px;top:130px;width:501px;height:32px">Subject</div>
  <div class="abs field" style="left:50px;top:182px;width:501px;height:92px">Write Your Message Here...</div>
  <span class="abs btn-send">SEND MESSAGE</span>
</section>
<section class="abs door" role="img" aria-label="Open French doors with retractable screens leading to a wooded balcony"></section>
<div class="abs door-floor"></div>
<div class="abs mail-mark"></div>

<svg width="0" height="0" style="position:absolute"><defs><symbol id="plus" viewBox="0 0 17 17"><circle cx="8.5" cy="8.5" r="7.5" fill="rgba(255,255,255,.25)" stroke="#fff" stroke-width="1.5"/><path d="M8.5 4.5v8M4.5 8.5h8" stroke="#fff" stroke-width="1.5"/></symbol></defs></svg>

<svg class="abs plus" style="left:927px;top:988px"><use href="#plus"/></svg>
<span class="abs hotspot" style="left:948px;top:986px">Optional anti-slam system</span>
<span class="abs hotspot" style="left:643px;top:1025px">Fits all door types</span>
<svg class="abs plus" style="left:777px;top:1027px"><use href="#plus"/></svg>
<span class="abs hotspot" style="left:700px;top:1103px">Various mesh options</span>
<svg class="abs plus" style="left:854px;top:1105px"><use href="#plus"/></svg>
<svg class="abs plus" style="left:1012px;top:1085px"><use href="#plus"/></svg>
<span class="abs hotspot" style="left:1032px;top:1075px">Wide range<br>of finishes</span>
<span class="abs hotspot" style="left:643px;top:1185px;text-align:right">Maintains décor<br>&amp; view</span>
<svg class="abs plus" style="left:767px;top:1195px"><use href="#plus"/></svg>
<svg class="abs plus" style="left:904px;top:1231px"><use href="#plus"/></svg>
<span class="abs hotspot" style="left:922px;top:1229px">Operates easily with slidebar</span>
<span class="abs hotspot" style="left:663px;top:1253px">Comes with warranty</span>
<svg class="abs plus" style="left:822px;top:1255px"><use href="#plus"/></svg>
<svg class="abs plus" style="left:952px;top:1293px"><use href="#plus"/></svg>
<span class="abs hotspot" style="left:974px;top:1291px">Glides smoothly along tracks</span>

<h2 class="abs section-title" style="top:1330px">Latest <span>Projects</span></h2>
<div class="abs green-rule" style="top:1370px"></div>
<div class="abs project" style="left:0;background:radial-gradient(ellipse 90px 60px at 170px 60px,rgba(255,240,210,.8),rgba(255,240,210,0)),linear-gradient(180deg,#5a4330 0%,#a08a70 35%,#d8cbb5 55%,#7a6450 75%,#4a3626 100%)" role="img" aria-label="Great room with stone fireplace and window shades"></div>
<div class="abs project" style="left:240px;background:linear-gradient(90deg,#8e8c86 0%,#eceae4 20%,#ffffff 40%,#d9d6cf 60%,#f0eee8 75%,#6e6a62 100%)" role="img" aria-label="White living room with sheer shades"></div>
<div class="abs project" style="left:480px;background:radial-gradient(ellipse 70px 50px at 120px 100px,rgba(240,240,240,.7),rgba(240,240,240,0)),linear-gradient(180deg,#4f6890 0%,#8ea3bf 40%,#6b7488 60%,#4a4e4a 80%,#3a4a2e 100%)" role="img" aria-label="Rooftop pavilion at dusk"></div>
<div class="abs project" style="left:720px;background:linear-gradient(180deg,#6a4426 0%,#8a5a32 12%,#efe6d4 30%,#ddd0b8 60%,#5a4634 80%,#3a2a1e 100%)" role="img" aria-label="Living room with Christmas tree and solar shades"></div>
<div class="abs project" style="left:960px;background:linear-gradient(180deg,#5f6870 0%,#8a949c 20%,#a9c4dc 40%,#8aa3b4 55%,#6a8a52 75%,#4a6a38 100%)" role="img" aria-label="Pergola roof overlooking mountains"></div>

<section class="abs reviews">
  <h2 class="abs section-title" style="top:16px">What <span>People Say</span></h2>
  <div class="abs green-rule" style="top:57px"></div>
  <p class="abs quote" style="left:52px;top:98px;width:408px;text-align:right">Duis aute irure dolor in reprehenderit in voluptate velit esse cillum dolore eu fugiat nulla pariatur. Excepteur sint occaecat cupidatat non proident, sunt in culpa qui officia deserunt mollit.</p>
  <span class="abs reviewer" style="left:52px;top:172px;width:408px;text-align:right">Miles Arden, Operations Manager</span>
  <div class="abs avatar" style="left:490px;top:98px;background:#c9b4a0" role="img" aria-label="Portrait of Miles Arden"></div>
  <div class="abs" style="left:598px;top:104px;height:72px;border-left:2px dotted #bbb"></div>
  <div class="abs avatar" style="left:633px;top:98px;background:#b89a86" role="img" aria-label="Portrait of Nora Vesk"></div>
  <p class="abs quote" style="left:738px;top:98px;width:410px">Provident, similique sunt in culpa qui officia deserunt mollitia animi, id est laborum et dolorum fuga. Et harum quidem rerum facilis est et expedita distinctio. Nam libero tempore, cum soluta nobis.</p>
  <span class="abs reviewer" style="left:738px;top:172px">Nora Vesk, Creative Designer</span>
</section>

<div class="abs like-rule"></div>
<div class="abs like-pill"></div>
<svg class="abs" style="left:399px;top:1847px" width="20" height="20" viewBox="0 0 20 20"><path d="M3 9h3v9H3z M7 9l4-7c2 0 2 2 1.5 4H17c1 0 1.6 1 1.3 2l-2 8c-.2.7-.8 1-1.5 1H7z" fill="none" stroke="#aaa" stroke-width="1.4"/></svg>
<div class="abs" style="left:435px;top:1835px;height:44px;border-left:1px solid #ddd"></div>
<span class="abs like-btn"><svg width="10" height="10" viewBox="0 0 10 10"><path d="M1 5l3 3 5-6" fill="none" stroke="#fff" stroke-width="1.8"/></svg>Like</span>
<span class="abs like-text">You and 4.1k others like this.</span>

<footer class="abs footer">
  <h3 style="left:52px;top:22px">Contact Us</h3>
  <p style="left:52px;top:62px;width:255px">Please feel free to contact us for any issue. Our staff is available to you from 9AM until 5PM on weekdays.</p>
  <span class="line" style="left:52px;top:136px"><strong>Phone:</strong> +1 416-555-0143</span>
  <span class="line" style="left:52px;top:170px"><strong>Office:</strong> 48 Larkspur Lane Coquitlam</span>
  <span class="line" style="left:52px;top:204px"><strong>Email:</strong> info@velmarix.ca</span>
  <span class="abs social" style="left:52px;top:243px"></span>
  <span class="abs social" style="left:76px;top:243px"></span>
  <span class="abs social" style="left:100px;top:243px"></span>
  <span class="abs social" style="left:136px;top:243px"></span>
  <span class="abs social" style="left:160px;top:243px"></span>

  <h3 style="left:0;width:1200px;text-align:center;top:22px">Headquarters</h3>
  <div class="abs map" role="img" aria-label="Map showing the headquarters location"></div>

  <h3 style="left:896px;top:22px">About Team</h3>
  <p style="left:896px;top:62px;width:252px">Enim congue blandit. Lorem ipsum dolor sit amet, consectetur adipiscing elit. Quisque consectetur interdum finibus. Vestibulum ante ipsum primis in faucibus orci. luctus et ultrices posuere.</p>
  <p style="left:896px;top:172px;width:252px">Cubilia cras blandit finibus ipsum, id porttitor arcu volutpat a. Integer iaculis erat nec justo malesuada faucibus vel tempus sapien. Vivamus aliquam euismod tristique.</p>

  <div class="abs footer-rule"></div>
  <span class="abs footer-small" style="left:52px">Copyright © Velmarix Inc</span>
  <div class="abs" style="left:530px;top:364px;display:flex;align-items:center;gap:8px">
    <span style="width:30px;height:30px;border-radius:50%;border:2px solid #fff"></span>
    <span style="font-size:22px;font-weight:500;color:#fff">Velmarix</span>
  </div>
  <span class="abs footer-small" style="right:52px">All rights reserved</span>
</footer>

</body>
</html>
```